Business Card Design For A Cajun Seafood Restaurant

We are opening a cajun seafood restaurant in a week. We mainly serve cajun seafood which is orginally from Louisiana. We want design on both sides of a business card. I have menu on the website. You can go to www.reednkettle.example to check out our menu.

Restaurant name: Reed N' Kettle
Phone: +1 (555) 304-7712
Address: 48206 Ludlow Row, #7, Bexmoor Flats, Ca90000
Email: reednkettle@mailbox.example
Website: www.reednkettle.example

Maybe add social media icons (facebook, instagram) if looks nice on the business card.
facebook.com/reednkettle
instagram.com/reednkettle or @reednkettle

Attached is the logo and other business card samples that I like.

```html
<!DOCTYPE html>
<html lang="en">
<head>
<meta charset="utf-8">
<title>Reed N' Kettle — Business Card</title>
<link rel="stylesheet" href="https://fonts.googleapis.com/css2?family=Source+Sans+3:wght@400;600;700&display=swap">
<style>
  :root {
    --page-bg: #3b3b3b;
    --card-white: #f7f7f7;
    --card-black: #000000;
    --accent-orange: #f26a0c;
    --ink-dark: #1a1a1a;
    --ink-grey: #4a4a4a;
    --ink-light: #f2f2f2;
    --art-orange: #e8691c;
    --art-gold: #f2c230;
  }
  * { box-sizing: border-box; margin: 0; padding: 0; }
  html, body {
    width: 1200px; height: 750px; overflow: hidden;
    background: var(--page-bg);
    font-family: "Source Sans 3", "Helvetica Neue", Arial, sans-serif;
  }
  .card {
    position: absolute; top: 228px;
    width: 462px; height: 262px;
    border-radius: 9px; overflow: hidden;
  }
  .card--front { left: 124px; background: var(--accent-orange); }
  .card--back { left: 618px; background: var(--card-black); }

  .front-shapes { position: absolute; inset: 0; }

  .illustration {
    position: absolute;
    border-radius: 50%;
    background: radial-gradient(circle closest-side at 50% 42%, var(--art-gold) 0%, var(--art-gold) 38%, var(--art-orange) 62%, var(--art-orange) 100%);
  }
  .illustration--logo { left: 80px; top: 22px; width: 74px; height: 70px; }
  .illustration--corner { left: 266px; top: 198px; width: 54px; height: 54px; }
  .illustration--hero { left: 150px; top: 50px; width: 164px; height: 160px; }

  .brand-name {
    position: absolute; left: 26px; top: 93px; width: 174px;
    text-align: center;
    font-size: 19px; font-weight: 700; color: var(--ink-dark);
    letter-spacing: 0.5px;
  }

  .person {
    position: absolute; right: 70px; top: 88px; text-align: right;
  }
  .person__name { font-size: 19px; font-weight: 600; color: var(--accent-orange); line-height: 1.1; }
  .person__title { font-size: 14px; color: var(--ink-dark); line-height: 1.25; }

  .address {
    position: absolute; left: 26px; top: 151px;
    font-size: 13px; line-height: 17px; color: var(--ink-grey); font-style: normal;
  }
  .contact-list {
    position: absolute; left: 26px; top: 191px; list-style: none;
    font-size: 13px; line-height: 17.5px; color: var(--ink-grey);
  }
  .contact-list li { display: flex; align-items: center; gap: 6px; }
  .contact-list svg { width: 11px; height: 11px; flex: none; }

  .social {
    position: absolute; left: 0; right: 0; top: 222px;
    display: flex; justify-content: center; align-items: center; gap: 4px;
    font-size: 13px; color: var(--ink-light);
  }
  .social__item { display: flex; align-items: center; gap: 4px; }
  .social__dot {
    width: 16px; height: 16px; border-radius: 50%;
    background: var(--accent-orange); display: inline-block;
  }
</style>
</head>
<body>

<section class="card card--front">
  <svg class="front-shapes" viewBox="0 0 462 262" width="462" height="262" aria-hidden="true">
    <path d="M0 0 H364 C420 50 445 130 426 190 C413 226 390 248 362 262 H0 Z" fill="var(--card-white)"/>
    <path d="M238 262 C330 242 405 182 429 108 C438 162 420 218 374 262 Z" fill="var(--card-black)"/>
  </svg>

  <div class="illustration illustration--logo" role="img" aria-label="Cartoon crab holding an ear of corn"></div>
  <div class="brand-name">Reed N' Kettle</div>

  <div class="person">
    <div class="person__name">DALE MARSH</div>
    <div class="person__title">CEO/Founder</div>
  </div>

  <address class="address">
    48206 Ludlow Row, #7<br>
    Bexmoor Flats, Ca90000
  </address>

  <ul class="contact-list">
    <li>
      <svg viewBox="0 0 12 12" aria-hidden="true"><path d="M2.5 1 L4.3 1 L5 3.6 L3.8 4.6 C4.5 6 5.8 7.4 7.4 8.2 L8.4 7 L11 7.7 L11 9.5 C11 10.4 10.3 11 9.4 11 C5 10.7 1.3 7 1 2.6 C1 1.7 1.6 1 2.5 1 Z" fill="var(--accent-orange)"/></svg>
      +1 (555) 304-7712
    </li>
    <li>
      <svg viewBox="0 0 12 12" aria-hidden="true"><rect x="0.5" y="2.5" width="11" height="7.5" fill="var(--accent-orange)"/><path d="M0.8 3 L6 7 L11.2 3" stroke="#fff" stroke-width="1" fill="none"/></svg>
      reednkettle@mailbox.example
    </li>
    <li>
      <svg viewBox="0 0 12 12" aria-hidden="true"><circle cx="6" cy="6" r="5.5" fill="var(--accent-orange)"/><path d="M6 0.5 V11.5 M0.5 6 H11.5 M2 3 C4.5 4.3 7.5 4.3 10 3 M2 9 C4.5 7.7 7.5 7.7 10 9" stroke="#fff" stroke-width="0.8" fill="none"/></svg>
      www.reednkettle.example
    </li>
  </ul>

  <div class="illustration illustration--corner" role="img" aria-label="Small cartoon crab holding an ear of corn"></div>
</section>

<section class="card card--back">
  <div class="illustration illustration--hero" role="img" aria-label="Cartoon crab lifting an ear of corn over its head"></div>
  <div class="social">
    <span class="social__item"><span class="social__dot"></span>reednkettle</span>
    <span class="social__item"><span class="social__dot"></span>@reednkettle</span>
  </div>
</section>

</body>
</html>
```